Business Card for Industrial Distributor

We need a business card design for an industrial distributor. We sell machine parts for the manufacturing and oil industry. We would like the cards to look clean and modern but with a touch of industry.

Our colors are blue/white.

Please feel free to visit our website www.korvelpartsco.com

Target Market(s)

mexican manufacturers in the automobile/aerospace industry

Industry/Entity Type

Industrial

Colors
ffffff
0555a3

```html
<!DOCTYPE html>
<html lang="en">
<head>
<meta charset="utf-8">
<title>Korvel – Business Card</title>
<link rel="stylesheet" href="https://fonts.googleapis.com/css2?family=Open+Sans:wght@400;600;800&display=swap">
<style>
  :root {
    --page: #e9e9ec;
    --white: #ffffff;
    --paper: #f4f4f4;
    --blue: #3147c2;
    --blue-light: #3d56d2;
    --blue-dark: #2638a8;
    --grey: #9b9b9b;
    --grey-text: #e4e4e4;
    --ink-soft: rgba(255,255,255,0.55);
  }
  * { box-sizing: border-box; margin: 0; padding: 0; }
  html, body {
    width: 1200px; height: 780px; overflow: hidden;
    background: var(--page);
    font-family: "Open Sans", Arial, sans-serif;
  }
  .sheet {
    width: 1200px; height: 780px;
    display: flex; align-items: center; justify-content: center; gap: 40px;
  }
  .card {
    width: 540px; height: 309px;
    position: relative; overflow: hidden;
    box-shadow: 0 6px 18px rgba(0,0,0,0.18);
    display: flex; flex-direction: column;
  }

  /* Front */
  .front__brand {
    height: 145px;
    background: linear-gradient(180deg, var(--white), var(--paper));
    display: flex; align-items: center; padding-left: 46px; gap: 18px;
  }
  .brand-dot {
    width: 64px; height: 64px; border-radius: 50%;
    background: var(--blue);
  }
  .brand-name {
    font-weight: 800; font-size: 74px; line-height: 1;
    color: var(--blue); letter-spacing: -1px;
  }
  .front__band {
    height: 124px;
    background: radial-gradient(ellipse at 60% 40%, var(--blue-light), var(--blue) 60%, var(--blue-dark));
    display: flex; align-items: center; padding: 0 30px 0 46px;
  }
  .holder { width: 170px; color: var(--white); }
  .holder__name { font-weight: 800; font-size: 17px; letter-spacing: 0.3px; }
  .holder__title { font-size: 13px; margin-top: 1px; }
  .divider { width: 1px; height: 78px; background: var(--ink-soft); margin-right: 22px; }
  .contacts { list-style: none; color: var(--white); font-size: 13.5px; line-height: 20px; }
  .contacts li { display: flex; align-items: center; gap: 8px; }
  .contacts svg { width: 13px; height: 13px; flex: none; }
  .front__strip, .back__strip {
    height: 40px; background: var(--grey);
    display: flex; align-items: center;
    color: var(--grey-text); font-size: 14px;
  }
  .front__strip { padding-left: 46px; }

  /* Back */
  .back__field {
    flex: 1;
    background: radial-gradient(ellipse at 50% 45%, var(--blue-light), var(--blue) 55%, var(--blue-dark));
    display: flex; align-items: center; justify-content: center;
  }
  .back__name {
    font-weight: 800; font-size: 92px; line-height: 1;
    color: var(--white); letter-spacing: -1px;
  }
  .back__strip { padding-left: 46px; font-size: 13px; }
</style>
</head>
<body>
<main class="sheet">

  <section class="card card--front" aria-label="Business card front">
    <div class="front__brand">
      <span class="brand-dot"></span>
      <span class="brand-name">Korvel</span>
    </div>
    <div class="front__band">
      <div class="holder">
        <p class="holder__name">DANIEL REYES</p>
        <p class="holder__title">Manager</p>
      </div>
      <span class="divider"></span>
      <ul class="contacts">
        <li>
          <svg viewBox="0 0 14 14" aria-hidden="true"><rect width="14" height="14" rx="2" fill="#fff"/><path d="M4 3.5l1.6 0 .8 2-1 .8a6 6 0 0 0 2.3 2.3l.8-1 2 .8v1.6c-3.6.3-6.8-2.9-6.5-6.5z" fill="#3147c2"/></svg>
          (555) 310 - 4820
        </li>
        <li>
          <svg viewBox="0 0 14 14" aria-hidden="true"><rect width="14" height="14" rx="2" fill="#fff"/><rect x="3" y="5" width="8" height="5" fill="#3147c2"/><rect x="4.5" y="3" width="5" height="2.5" fill="#3147c2"/></svg>
          (555) 310 - 4827
        </li>
        <li>
          <svg viewBox="0 0 14 14" aria-hidden="true"><rect width="14" height="14" rx="2" fill="#fff"/><rect x="2.5" y="4" width="9" height="6" fill="none" stroke="#3147c2" stroke-width="1.2"/><path d="M2.5 4l4.5 3.5L11.5 4" fill="none" stroke="#3147c2" stroke-width="1.2"/></svg>
          sales@korvelpartsco.com
        </li>
        <li>
          <svg viewBox="0 0 14 14" aria-hidden="true"><rect width="14" height="14" rx="2" fill="#fff"/><circle cx="7" cy="7" r="4.3" fill="none" stroke="#3147c2" stroke-width="1.1"/><path d="M2.7 7h8.6M7 2.7c-2 2.5-2 6.1 0 8.6M7 2.7c2 2.5 2 6.1 0 8.6" fill="none" stroke="#3147c2" stroke-width="0.9"/></svg>
          www.korvelpartsco.com
        </li>
      </ul>
    </div>
    <div class="front__strip">4120 Harbor Mill Rd. Laredo, TX 78041</div>
  </section>

  <section class="card card--back" aria-label="Business card back">
    <div class="back__field">
      <span class="back__name">Korvel</span>
    </div>
    <div class="back__strip">www.korvelpartsco.com</div>
  </section>

</main>
</body>
</html>
```